IT Company requires new Business Card design.

Over the years we have had a few different business card designs. We are now due for new cards across the board for all staff. We felt this would be a good time to start fresh with a new design. Our traditional card simply had our details on the front, and a list of services on the back. We don't particularly need the list of services, we have had cards where the only thing on the rear of the card was our logo.
Feel free to be creative, we would like our tag line "Complete IT Management" to appear at some point, doesn't necessarily have to be with the logo.
I have attached samples and drafts of various previous cards we have used over the years.

```html
<!DOCTYPE html>
<html lang="en">
<head>
<meta charset="utf-8">
<title>Harbor Systems – Business Card</title>
<link href="https://fonts.googleapis.com/css2?family=Open+Sans:wght@400;600;700&display=swap" rel="stylesheet">
<style>
  :root {
    --page-bg: #e6e7e8;
    --card-bg: #ffffff;
    --slate: #5f6e7a;
    --slate-light: #6b7a86;
    --charcoal: #4b4c4e;
    --text: #333a40;
    --muted: #5a6168;
  }
  * { margin: 0; padding: 0; box-sizing: border-box; }
  html, body {
    width: 1034px; height: 1200px; overflow: hidden;
    background: var(--page-bg);
    font-family: "Open Sans", Arial, sans-serif;
  }
  .card {
    position: absolute; left: 74px; width: 898px; height: 511px;
    background: var(--card-bg); border-radius: 42px; overflow: hidden;
    box-shadow: 0 2px 6px rgba(0,0,0,0.12);
  }
  .card--front { top: 69px; }
  .card--back { top: 628px; }

  .accent-bar { position: absolute; left: 0; top: 48px; width: 19px; height: 75px; background: var(--slate); }
  .holder-name { position: absolute; left: 46px; top: 48px; font-size: 28px; font-weight: 700; color: var(--slate); }
  .holder-title { position: absolute; left: 46px; top: 88px; font-size: 21px; color: var(--muted); }
  .address { position: absolute; left: 46px; top: 156px; font-size: 21px; line-height: 31px; color: var(--text); }

  .contacts { position: absolute; left: 32px; top: 250px; list-style: none; }
  .contacts li { display: flex; align-items: center; height: 35px; font-size: 21px; color: var(--text); }
  .contacts svg { width: 22px; height: 22px; margin-right: 24px; fill: var(--muted); flex: none; }

  .brand { position: absolute; display: flex; align-items: center; color: var(--slate); font-weight: 700; }
  .brand-mark { background: var(--slate); flex: none; }
  .brand-name { line-height: 1.0; letter-spacing: 1px; }
  .brand--front { left: 440px; top: 160px; }
  .brand--front .brand-mark { width: 110px; height: 110px; margin-right: 28px; }
  .brand--front .brand-name { font-size: 54px; }
  .brand--back { left: 175px; top: 170px; }
  .brand--back .brand-mark { width: 170px; height: 170px; margin-right: 36px; }
  .brand--back .brand-name { font-size: 76px; }

  .tagline-band { position: absolute; left: 0; right: 0; top: 442px; height: 40px; }
  .tagline-band svg { position: absolute; inset: 0; width: 100%; height: 100%; }
  .tagline { position: absolute; left: 46px; top: 5px; font-size: 21px; font-weight: 700; color: #fff; }

  .website { position: absolute; left: 0; right: 0; top: 452px; text-align: center; font-size: 25px; letter-spacing: 2px; color: var(--charcoal); }
</style>
</head>
<body>

<section class="card card--front" aria-label="Card front">
  <div class="accent-bar"></div>
  <h1 class="holder-name">Mark Ellison</h1>
  <p class="holder-title">Operation Manager</p>
  <p class="address">Unit 7 22 Harbour Reach<br>Bayview WA 6170</p>

  <ul class="contacts">
    <li><svg viewBox="0 0 24 24" aria-hidden="true"><circle cx="12" cy="12" r="11" fill="none" stroke="#5a6168" stroke-width="2"/><path d="M8 6.5l2 0 1 3-1.5 1a7 7 0 0 0 4 4l1-1.5 3 1v2a1.5 1.5 0 0 1-1.5 1.5A10 10 0 0 1 6.5 8 1.5 1.5 0 0 1 8 6.5z"/></svg>08 9350 4812</li>
    <li><svg viewBox="0 0 24 24" aria-hidden="true"><rect x="6" y="1" width="12" height="22" rx="2"/><rect x="8" y="4" width="8" height="9" fill="#fff"/><circle cx="12" cy="18" r="1.6" fill="#fff"/></svg>0412 738 194</li>
    <li><svg viewBox="0 0 24 24" aria-hidden="true"><rect x="6" y="2" width="12" height="8" fill="none" stroke="#5a6168" stroke-width="2"/><rect x="1" y="10" width="22" height="10" rx="2"/><rect x="6" y="15" width="12" height="7" fill="#5a6168" stroke="#fff" stroke-width="1.5"/></svg>08 9350 4812</li>
    <li><svg viewBox="0 0 24 24" aria-hidden="true"><rect x="1" y="5" width="22" height="15" rx="2"/><path d="M2 6l10 8 10-8" fill="none" stroke="#fff" stroke-width="2"/></svg>mark@harborsystems.com.au</li>
    <li><svg viewBox="0 0 24 24" aria-hidden="true"><circle cx="12" cy="12" r="10.5" fill="none" stroke="#5a6168" stroke-width="2"/><ellipse cx="12" cy="12" rx="4.5" ry="10.5" fill="none" stroke="#5a6168" stroke-width="1.6"/><path d="M2 12h20M4 6.5h16M4 17.5h16" stroke="#5a6168" stroke-width="1.6"/></svg>www.harborsystems.com.au</li>
  </ul>

  <div class="brand brand--front">
    <span class="brand-mark"></span>
    <span class="brand-name">HARBOR<br>SYSTEMS</span>
  </div>

  <div class="tagline-band">
    <svg viewBox="0 0 898 40" preserveAspectRatio="none" aria-hidden="true">
      <rect x="0" y="0" width="898" height="40" fill="#4b4c4e"/>
      <path d="M0 0H568L590 28Q596 36 586 40H0Z" fill="#6b7a86"/>
    </svg>
    <p class="tagline">Complete IT Management</p>
  </div>
</section>

<section class="card card--back" aria-label="Card back">
  <div class="brand brand--back">
    <span class="brand-mark"></span>
    <span class="brand-name">HARBOR<br>SYSTEMS</span>
  </div>
  <p class="website">www.harborsystems.com.au</p>
</section>

</body>
</html>
```